WordPress Design for both website and landing page for an expert

I need a clean and stylish design for my new website. I work as an expert (see attached file WHY HOW WHAT), my product is expert opinion (reports) for company evaluations You can use all of the attached pictures colored or black / white. The person is me, you can add other pictures, if you want. The design should be clean and stylish, so you could use white, black, gray, silver and / or one additional color. I have added an idea about my website, see attached file CONCEPT WEBSITE If you have any more information, please do not hesitate to contact us 'Hesitate to ask me ...

```html
<!DOCTYPE html>
<html lang="de">
<head>
<meta charset="utf-8">
<title>Lukas Brenner – Sachverständiger für Firmenbewertungen</title>
<link rel="stylesheet" href="https://fonts.googleapis.com/css2?family=Montserrat:wght@400;500;600;700&family=Open+Sans:wght@400;600&display=swap">
<style>
:root{
  --slate:#7d858c;
  --slate-dark:#5f676e;
  --black:#000;
  --white:#fff;
  --mist:#efefef;
  --ink:#222;
  --text:#555a5f;
  --heading:#7b848b;
}
*{box-sizing:border-box;margin:0;padding:0}
html,body{width:1200px;height:2956px;overflow:hidden}
body{font-family:"Open Sans",Arial,sans-serif;color:var(--text);background:var(--white);position:relative}
.page{position:relative;width:1200px;height:2956px}
section,header,footer{position:absolute;left:0;width:1200px}

.topbar{top:0;height:52px;background:var(--slate);color:var(--white);font-size:15px;font-family:"Montserrat",sans-serif}
.topbar .contact{position:absolute;left:90px;top:16px;display:flex;gap:22px;align-items:center}
.topbar .contact span{display:flex;align-items:center;gap:7px}
.topbar .social{position:absolute;right:96px;top:19px;display:flex;gap:10px}
.dot{width:14px;height:14px;border-radius:50%;background:var(--white);opacity:.9}

.masthead{top:52px;height:113px;background:var(--black)}
.brand{position:absolute;left:90px;top:30px;display:flex;align-items:center;gap:14px;color:var(--white);font-family:"Montserrat",sans-serif;font-size:24px;font-weight:400;letter-spacing:4px}
.brand .mark{width:26px;height:26px;border:2px solid var(--white);border-radius:50%}
.nav{position:absolute;right:98px;top:44px;display:flex;gap:30px;font-family:"Montserrat",sans-serif;font-size:15px;color:var(--white)}

.hero{top:165px;height:535px;overflow:hidden;background:linear-gradient(90deg,#b9b3ad 0%,#d8d6d2 45%,#e4e3e0 100%)}
.hero .photo{position:absolute;left:0;top:0;width:640px;height:535px;background:radial-gradient(ellipse at 35% 45%,#9c8f86 0%,#c5bfb8 55%,rgba(216,214,210,0) 80%)}
.hero .copy{position:absolute;left:640px;top:140px;color:var(--ink);font-family:"Montserrat",sans-serif}
.hero h1{font-size:40px;font-weight:600;letter-spacing:.5px;line-height:1.15}
.hero h2{font-size:30px;font-weight:600;line-height:1.3}
.hero p{font-size:21px;line-height:40px;margin-top:6px;font-weight:400}
.btn{display:inline-flex;align-items:center;justify-content:center;gap:9px;background:var(--slate);color:var(--white);font-family:"Montserrat",sans-serif;font-weight:600;font-size:16px;border-radius:30px;box-shadow:0 3px 6px rgba(0,0,0,.25)}
.hero .btn{margin-top:20px;width:202px;height:54px}
.hero .wave{position:absolute;left:0;bottom:-1px}

.why{top:700px;height:720px;background:var(--mist);text-align:center}
.why h3{position:absolute;top:66px;width:100%;font-family:"Montserrat",sans-serif;font-weight:400;font-size:34px;color:var(--heading)}
.why .links{position:absolute;left:0;top:120px}
.feature{position:absolute;top:370px;width:300px;text-align:center}
.feature h4{margin-top:12px;font-family:"Montserrat",sans-serif;font-size:17px;font-weight:600;color:var(--slate-dark)}
.feature p{margin-top:12px;font-size:13.5px;line-height:25px;color:#333}
.why .note{position:absolute;top:520px;width:100%;font-family:"Montserrat",sans-serif;font-size:18px;line-height:35px;color:#222}
.why .btn{position:absolute;left:507px;top:594px;width:186px;height:50px}

.about{top:1420px;height:570px}
.about .photo{position:absolute;left:0;top:0;width:600px;height:570px;background:linear-gradient(90deg,#8c8985 0%,#b9b6b1 40%,#d7d5d1 100%)}
.about .copy{position:absolute;left:625px;top:58px;width:460px}
.section-title{font-family:"Montserrat",sans-serif;font-size:31px;color:var(--heading);font-weight:400;letter-spacing:1px}
.section-title strong{font-weight:600}
.about p{margin-top:20px;font-size:13.5px;line-height:24px;color:#555;text-align:justify}
.about .actions{display:flex;gap:14px;margin-top:28px}
.about .btn{width:202px;height:54px}
.curve{position:absolute;top:0}

.motives{top:1990px;height:570px}
.motives .photo{position:absolute;left:600px;top:0;width:600px;height:570px;background:linear-gradient(135deg,#e7dccb 0%,#d7d4cf 45%,#a8aeb4 100%)}
.motives .copy{position:absolute;left:110px;top:62px;width:464px}
.motives h3{font-family:"Montserrat",sans-serif;font-size:19.5px;font-weight:400;line-height:31px;color:var(--heading)}
.motives ul{list-style:none;margin-top:18px}
.motives li,.motives .para{font-size:13px;line-height:26.5px;color:#555;text-align:justify}
.motives .btn{margin-top:16px;width:202px;height:54px}

.cta{top:2560px;height:218px;background:var(--mist);text-align:center}
.cta p{position:absolute;top:44px;width:100%;font-family:"Montserrat",sans-serif;font-size:18px;line-height:35px;color:#222}
.cta .btn{position:absolute;left:453px;top:122px;width:294px;height:50px}

.footer{top:2778px;height:178px;background:var(--white)}
.footer .brand{top:70px;color:var(--slate);font-size:24px}
.footer .brand .mark{border-color:var(--slate)}
.footer .nav{left:398px;right:auto;top:98px;color:#222;font-size:14px;gap:26px}
.footer .copyright{position:absolute;left:485px;top:130px;font-size:13px;color:#555}
.footer .social{position:absolute;left:955px;top:103px;display:flex;gap:12px}
.footer .social span{width:36px;height:36px;border:1.5px solid #b7bcc0;border-radius:50%}
</style>
</head>
<body>
<div class="page">

<header class="topbar">
  <div class="contact">
    <span><svg width="14" height="14" viewBox="0 0 24 24" fill="#fff"><path d="M6.6 10.8a15.1 15.1 0 006.6 6.6l2.2-2.2a1 1 0 011-.25 11.4 11.4 0 003.6.57 1 1 0 011 1V20a1 1 0 01-1 1A17 17 0 013 4a1 1 0 011-1h3.5a1 1 0 011 1c0 1.25.2 2.45.57 3.57a1 1 0 01-.25 1z"/></svg>Call us on : (425) 555-0148</span>
    <span><svg width="15" height="12" viewBox="0 0 24 18" fill="#fff"><path d="M0 0h24v2L12 10 0 2z M0 5l12 8 12-8v13H0z"/></svg>Mail us on: info@lukasbrenner-gutachten.de</span>
  </div>
  <div class="social"><span class="dot"></span><span class="dot"></span><span class="dot"></span><span class="dot"></span></div>
</header>

<header class="masthead">
  <div class="brand"><span class="mark"></span>LUKAS BRENNER</div>
  <nav class="nav"><span>Home</span><span>what I do</span><span>why I do it &amp; How I do it</span><span>about me</span><span>Contact</span></nav>
</header>

<section class="hero">
  <div class="photo" role="img" aria-label="Portrait of the consultant in a white shirt leaning on a railing in a bright office"></div>
  <div class="copy">
    <h1>SACHVERSTÄNDIGER</h1>
    <h2>FÜR FIRMENBEWERTUNGEN</h2>
    <p>Sie benötigen ein Gutachten zur Ermittlung<br>des Wertes Ihres Unternehmens</p>
    <span class="btn"><svg width="12" height="14" viewBox="0 0 12 14" fill="#fff"><path d="M0 0h8l4 4v10H0z"/></svg>Read More</span>
  </div>
  <svg class="wave" width="1200" height="60" viewBox="0 0 1200 60">
    <path d="M0 60 L420 60 C500 60 520 22 600 22 C680 22 700 60 780 60 L1200 60Z" fill="#efefef"/>
    <path d="M589 40 L600 50 L611 40" stroke="#7d858c" stroke-width="3" fill="none"/>
  </svg>
</section>

<section class="why">
  <h3>Why you should work with me</h3>
  <svg class="links" width="1200" height="260" viewBox="0 0 1200 260">
    <path d="M314 140 C380 95 440 110 515 125" stroke="#888" stroke-width="2" stroke-dasharray="2 5" fill="none"/>
    <path d="M680 150 C760 200 820 190 880 150" stroke="#888" stroke-width="2" stroke-dasharray="2 5" fill="none"/>
    <g fill="#fff" stroke="#8a9095" stroke-width="2">
      <path d="M232 245 L214 225 A82 82 0 1 1 250 225 Z"/>
      <path d="M597 245 L579 225 A82 82 0 1 1 615 225 Z"/>
      <path d="M962 245 L944 225 A82 82 0 1 1 980 225 Z"/>
    </g>
    <g fill="#7d858c">
      <circle cx="232" cy="146" r="70"/><circle cx="597" cy="146" r="70"/><circle cx="962" cy="146" r="70"/>
    </g>
    <g fill="none" stroke="#fff" stroke-width="3">
      <rect x="208" y="112" width="42" height="56" rx="3"/><path d="M216 150h26M216 158h18"/><circle cx="232" cy="132" r="9"/>
      <circle cx="597" cy="146" r="36"/><rect x="565" y="136" width="64" height="20" rx="2" transform="rotate(-15 597 146)"/>
      <rect x="935" y="114" width="54" height="64" rx="3"/><path d="M944 128h36M944 138h16M944 148h16M944 158h36M944 168h36"/><rect x="966" y="136" width="14" height="14"/>
    </g>
  </svg>
  <div class="feature" style="left:82px">
    <h4>SCHNELL:</h4>
    <p>Sie bekommen Ihr Gutachten zeitnah<br>(innerhalb von max. 21 Tagen nach<br>Zugang aller benötigten Unterlagen)</p>
  </div>
  <div class="feature" style="left:447px">
    <h4>ZERTIFIZIERT:</h4>
    <p>Sie erhalten ein qualifiziertes und<br>belastbares Gutachten von einem zer-<br>tifizierten Sachverständigen (höchste</p>
  </div>
  <div class="feature" style="left:812px">
    <h4>VERSTÄNDLICH:</h4>
    <p>Ihr Gutachten wird für Sie logisch und<br>nachvollziehbar sein und kein "Fachchi-<br>nesisch" enthalten</p>
  </div>
  <p class="note">should the advised date for the preparation of the report be exceeded,<br>you will receive the report free of chare</p>
  <span class="btn">I waive my fee</span>
</section>

<section class="about">
  <div class="photo" role="img" aria-label="Portrait of the consultant in a dark suit walking through a modern hallway"></div>
  <svg class="curve" style="left:540px" width="80" height="570" viewBox="0 0 80 570">
    <path d="M60 0 C20 150 20 420 60 570 L80 570 L80 0Z" fill="#fff"/>
    <path d="M46 275 L36 285 L46 295" stroke="#333" stroke-width="2.5" fill="none"/>
  </svg>
  <div class="copy">
    <h3 class="section-title">ABOUT <strong>ME</strong></h3>
    <p>Sed ut perspiciatis unde omnis iste natus error sit voluptatem accusantium doloremque laudantium, totam rem aperiam, eaque ipsa quae ab illo inventore veritatis et quasi architecto beatae vitae dicta sunt explicabo. Nemo enim ipsam out odit aut fugit.</p>
    <p>Sed ut perspiciatis unde omnis iste natus error sit voluptatem accusantium doloremque laudantium, totam rem aperiam, eaque ipsa quae ab illo inventore veritatis et quasi architecto beatae vitae dicta sunt explicabo. Nemo enim ipsam out odit aut fugit.</p>
    <p>Sed ut perspiciatis unde omnis iste natus error sit voluptatem accusantium doloremque laudantium, totam rem aperiam, eaque ipsa quae ab illo inventore veritatis et quasi architecto beatae vitae dicta sunt explicabo. Nemo enim ipsam out odit aut fugit.</p>
    <div class="actions">
      <span class="btn"><svg width="12" height="14" viewBox="0 0 12 14" fill="#fff"><path d="M0 0h8l4 4v10H0z"/></svg>Read More</span>
      <span class="btn"><svg width="16" height="13" viewBox="0 0 16 13" fill="#fff"><path d="M0 1h6l2 2h8v10H0z"/></svg>Brenner Bio</span>
    </div>
  </div>
</section>

<section class="motives">
  <div class="photo" role="img" aria-label="Hand with a pen working through financial charts on paper"></div>
  <svg class="curve" style="left:580px" width="80" height="570" viewBox="0 0 80 570">
    <path d="M20 0 C60 150 60 420 20 570 L0 570 L0 0Z" fill="#fff"/>
    <path d="M36 275 L46 285 L36 295" stroke="#333" stroke-width="2.5" fill="none"/>
  </svg>
  <div class="copy">
    <h3>What are the buying motives of the customers?<br>Was sind die Kaufmotive der Kunden?</h3>
    <ul>
      <li>- Sie wollen Anteile Ihres Unternehmens oder ihr gesamtes Unternehmen verkaufen?</li>
      <li>- Sie wollen Ihr Unternehmen auf Ihre Erben übertragen und benötigen eine Bewertung für das Finanzamt?</li>
      <li>- Sie müssen im Rahmen einer Trennung/Scheidung jemanden ausbezahlen und benötigen eine Bemessungsgrundlage?</li>
    </ul>
    <p class="para">Lassen Sie Ihr Unternehmen von einem qualifizierten Sachverständigen bewerten und gehen somit vielen (unnötigen) Streitereien aus dem Weg.</p>
    <p class="para">Merke: Die Kosten für ein Gutachten sind immer überproportional günstiger als die Kosten für Rechtsstreitigkeiten. Und das losgelöst von der psychischen Belastung einer solchen Auseinandersetzung ...</p>
    <span class="btn"><svg width="12" height="14" viewBox="0 0 12 14" fill="#fff"><path d="M0 0h8l4 4v10H0z"/></svg>Read More</span>
  </div>
</section>

<section class="cta">
  <p>Sollte der avisierte Termin für die Erstellung des Gutachtens überschritten werden,<br>erhalten Sie das Gutachten absolut kostenfrei!</p>
  <span class="btn">Ich verzichte auf mein Honorar</span>
</section>

<footer class="footer">
  <div class="brand"><span class="mark"></span>LUKAS BRENNER</div>
  <nav class="nav"><span>Home</span><span>What I do</span><span>Why I do it</span><span>About me</span><span>Contact us</span></nav>
  <p class="copyright">Copyright © 2018. Allrights Reserved</p>
  <div class="social"><span></span><span></span><span></span></div>
</footer>

</div>
</body>
</html>
```